Website for "Bright Morrow Ltd" cleaning bsuiness

We require a website to expose our business to the local market. We want to provide background on who we are and what we do but in an easily digestible way. We clean domestic and commercial premises and want to provide a list of all of our services to potential customers. We operate out of Warrington in the UK.

We would like the website to be animated in some way so that the experience of using it is not dull or mundane. This website needs to be an extension of our company.

Target Market(s)

30 - 60 year olds for Domestic plus commercial clients

Industry/Entity Type

Cleaning Service

Coding

Coded - Design and coding required

Number of Pages Required

4 page

Font styles to use
Sans Serif

Colors
0455a3
3176b5
85acd3
cfdeed
ffffff
000000
1b1b1b
c8c8c8
757575

Requirements
Must have
• Logo which has been provided. Theme based around the logo and its colours. Simple layout to avoid confusion.
Nice to have
• Animations where possible to impress the customer.
Should not have
• any pictures of cleaning equipment, fairies, maids etc

```html
<!DOCTYPE html>
<html lang="en">
<head>
<meta charset="utf-8">
<title>Bright Morrow Ltd – Professional Cleaning Service</title>
<link rel="stylesheet" href="https://fonts.googleapis.com/css2?family=Open+Sans:wght@400;600&display=swap">
<style>
:root{
  --navy:#0455a3;
  --blue:#3176b5;
  --sky:#85acd3;
  --mist:#cfdeed;
  --white:#ffffff;
  --black:#000000;
  --dark:#1b1b1b;
  --grey:#c8c8c8;
  --mid:#757575;
}
*{box-sizing:border-box;margin:0;padding:0}
html,body{width:824px;height:1200px;overflow:hidden;background:var(--white);font-family:"Open Sans",Arial,sans-serif;color:var(--dark)}
.page{position:relative;width:824px;height:1200px}

/* header */
.site-header{position:absolute;top:0;left:0;width:824px;height:122px;background:var(--white)}
.brand{position:absolute;left:92px;top:36px;display:flex;align-items:center;gap:9px}
.brand-mark{width:30px;height:30px;background:var(--navy)}
.brand-name{font-size:24px;font-weight:600;color:var(--navy);line-height:1}
.brand-tag{position:absolute;left:92px;top:78px;font-size:10.5px;color:var(--dark);letter-spacing:.3px}
.contact{position:absolute;right:91px;top:33px;text-align:right}
.contact .address{font-size:8.4px;color:var(--dark)}
.contact .lines{margin-top:5px;font-size:11px;font-weight:600;color:var(--dark);display:flex;gap:8px;justify-content:flex-end;align-items:center}
.contact .lines svg{vertical-align:-1px;margin-right:3px}
.main-nav{position:absolute;right:91px;top:82px;display:flex;gap:21px;font-size:8.5px;color:var(--dark)}
.main-nav .current{color:var(--blue)}

/* hero */
.hero{position:absolute;top:122px;left:0;width:824px;height:299px;
  background:
    linear-gradient(180deg,rgba(255,255,255,0) 0%,rgba(255,255,255,0) 62%,rgba(250,251,252,.85) 78%,rgba(245,247,248,.95) 100%),
    linear-gradient(90deg,#f6f7f8 0%,#eef1f3 18%,#d9e2e7 30%,#c8d6dc 40%,#e9eef1 50%,#f4f6f7 56%,#d2dfe4 64%,#bccccf 76%,#aebfb8 88%,#c6d3d2 100%)}
.slide-arrow{position:absolute;width:17px;height:21px;background:rgba(120,120,120,.55);display:flex;align-items:center;justify-content:center}
.hero .slide-arrow{top:139px}
.slide-arrow.left{left:0}
.slide-arrow.right{right:0}

/* who we are */
.about{position:absolute;top:421px;left:0;width:824px;height:137px;background:linear-gradient(90deg,#0b7fd6 0%,#1398ee 50%,#0a7cd4 100%);color:var(--white);text-align:center}
.about h2{font-weight:400;font-size:19px;margin-top:30px}
.about p{font-size:9.8px;line-height:15.5px;width:650px;margin:5px auto 0}

/* services */
.services{position:absolute;top:558px;left:0;width:824px;height:455px;background:linear-gradient(180deg,#f6f7f8 0%,#eceef0 50%,#f3f4f5 100%)}
.services h2{position:absolute;top:34px;width:100%;text-align:center;font-weight:400;font-size:19px;color:var(--navy)}
.service{position:absolute;width:190px;text-align:center}
.service svg{display:block;margin:0 auto;height:30px}
.service h3{font-size:14px;font-weight:400;color:var(--navy);margin-top:6px;letter-spacing:.2px}
.service p{font-size:6.3px;line-height:9.6px;color:var(--mid);margin-top:2px}

/* gallery */
.gallery{position:absolute;top:1013px;left:0;width:824px;height:120px;display:flex}
.gallery .shot{flex:1;height:120px}
.shot.tower{background:linear-gradient(200deg,#f2f4f6 0%,#c9d0d8 30%,#5d6874 55%,#1e2731 80%,#3a4450 100%)}
.shot.stone{background:linear-gradient(90deg,#e9e8e3 0%,#dcdcd6 45%,#f0f0ec 60%,#c4c9c8 100%)}
.shot.office{background:linear-gradient(180deg,#5e98d6 0%,#a9c8e8 18%,#f2f3f2 40%,#cfdbe0 60%,#6f8ea3 78%,#8fa58c 100%)}
.shot.curve{background:linear-gradient(180deg,#6fa8de 0%,#b7d3ec 25%,#f1f1ee 45%,#d9cfbf 65%,#e6e6e2 78%,#7f9d4f 100%)}
.shot.lounge{background:linear-gradient(180deg,#f3f2ef 0%,#e6e3de 45%,#f7f7f5 68%,#c9a27a 85%,#a57a52 100%)}
.gallery .slide-arrow{top:50px}

/* footer */
.site-footer{position:absolute;top:1133px;left:0;width:824px;height:67px;background:var(--dark);color:var(--grey)}
.footer-nav{position:absolute;left:92px;top:22px;font-size:7px;display:flex;gap:6px}
.copyright{position:absolute;left:92px;top:40px;font-size:7px}
.social{position:absolute;right:92px;top:24px;display:flex;gap:4px}
.social span{width:17px;height:17px;border-radius:50%;background:var(--blue)}
.social span:nth-child(2){background:var(--sky)}
.social span:nth-child(3){background:var(--navy)}
.social span:nth-child(4){background:var(--mid)}
</style>
</head>
<body>
<div class="page">

<header class="site-header">
  <div class="brand"><span class="brand-mark"></span><span class="brand-name">Bright Morrow Ltd</span></div>
  <div class="brand-tag">Professional Cleaning Service</div>
  <div class="contact">
    <div class="address">24 Building name, Street name, City - Zipcode</div>
    <div class="lines">
      <span><svg width="6" height="9" viewBox="0 0 6 9"><rect x=".5" y=".5" width="5" height="8" rx="1" fill="none" stroke="#1b1b1b"/></svg>555 014 2290</span>
      <span>|</span>
      <span><svg width="10" height="8" viewBox="0 0 10 8"><rect width="10" height="8" rx="1" fill="#1b1b1b"/><path d="M0 1l5 3.5L10 1" stroke="#fff" fill="none"/></svg>info@brightmorrow.co.uk</span>
    </div>
  </div>
  <nav class="main-nav"><span class="current">Home</span><span>About Us</span><span>Services</span><span>Gallery</span><span>Contact Us</span></nav>
</header>

<section class="hero" role="img" aria-label="Bright white modern office lobby with curved reception desk, glass walls and a view of trees outside">
  <div class="slide-arrow left"><svg width="7" height="12" viewBox="0 0 7 12"><path d="M6 1L1 6l5 5" stroke="#fff" fill="none"/></svg></div>
  <div class="slide-arrow right"><svg width="7" height="12" viewBox="0 0 7 12"><path d="M1 1l5 5-5 5" stroke="#fff" fill="none"/></svg></div>
</section>

<section class="about">
  <h2>Who we are</h2>
  <p>Donec nec luctus tortor. Fusce imperdiet libero ipsum, vitae mattis velit mattis quis. Ut rutrum nibh justo, in interdum nulla sollicitudin nec. Aliquam posuere pharetra elit eleifend faucibus. Suspendisse potenti. Proin ultrices placerat purus non accumsan. Duis at odio sit amet ex interdum dictum. Nulla dictum, eros vel pulvinar pulvinar, felis massa bibendum</p>
</section>

<section class="services">
  <h2>What we do</h2>

  <div class="service" style="left:94px;top:86px">
    <svg viewBox="0 0 36 30" width="36"><rect x="0" y="2" width="36" height="24" fill="#0455a3"/><rect x="4" y="6" width="12" height="6" rx="2" fill="#fff"/><rect x="20" y="6" width="12" height="6" rx="2" fill="#fff"/><rect x="0" y="26" width="3" height="4" fill="#0455a3"/><rect x="33" y="26" width="3" height="4" fill="#0455a3"/></svg>
    <h3>BEDROOMS</h3>
    <p>Aliquam posuere pharetra elit eleifend faucibus. Suspendisse potenti. Proin ultrices placerat purus non accumsan. Duis at odio sit amet ex interdum dictum.</p>
  </div>
  <div class="service" style="left:317px;top:86px">
    <svg viewBox="0 0 26 30" width="26"><path d="M13 3a2 2 0 1 1 2 2l-2 2L2 13h22L13 7" stroke="#0455a3" stroke-width="2" fill="none"/><rect x="5" y="15" width="16" height="13" fill="#0455a3"/><rect x="5" y="19" width="16" height="2" fill="#fff"/></svg>
    <h3>BATHROOMS</h3>
    <p>Aliquam posuere pharetra elit eleifend faucibus. Suspendisse potenti. Proin ultrices placerat purus non accumsan. Duis at odio sit amet ex interdum dictum.</p>
  </div>
  <div class="service" style="left:540px;top:86px">
    <svg viewBox="0 0 28 30" width="28"><rect x="8" y="1" width="12" height="4" fill="#0455a3"/><circle cx="14" cy="17" r="12" fill="#0455a3"/><circle cx="14" cy="18" r="5" fill="#fff"/></svg>
    <h3>LIVINGROOMS</h3>
    <p>Aliquam posuere pharetra elit eleifend faucibus. Suspendisse potenti. Proin ultrices placerat purus non accumsan. Duis at odio sit amet ex interdum dictum.</p>
  </div>

  <div class="service" style="left:94px;top:207px">
    <svg viewBox="0 0 30 30" width="30"><rect width="30" height="30" fill="#0455a3"/><path d="M15 6c3 5 7 8 7 13a7 7 0 0 1-14 0c0-4 3-5 4-9 1 3 2 4 3 4 1-3 0-6 0-8z" fill="#fff"/></svg>
    <h3>KITCHEN</h3>
    <p>Aliquam posuere pharetra elit eleifend faucibus. Suspendisse potenti. Proin ultrices placerat purus non accumsan. Duis at odio sit amet ex interdum dictum.</p>
  </div>
  <div class="service" style="left:317px;top:207px">
    <svg viewBox="0 0 44 30" width="44"><circle cx="22" cy="4" r="3" fill="#0455a3"/><path d="M4 26a18 19 0 0 1 36 0z" fill="#0455a3"/><rect x="0" y="26" width="44" height="3" fill="#0455a3"/></svg>
    <h3>DINNING ROOMS</h3>
    <p>Aliquam posuere pharetra elit eleifend faucibus. Suspendisse potenti. Proin ultrices placerat purus non accumsan. Duis at odio sit amet ex interdum dictum.</p>
  </div>
  <div class="service" style="left:540px;top:207px">
    <svg viewBox="0 0 22 30" width="22"><rect width="22" height="30" fill="#0455a3"/><rect x="2" y="3" width="18" height="2" fill="#fff"/><circle cx="11" cy="17" r="6" fill="#fff"/><circle cx="11" cy="17" r="3" fill="#0455a3"/></svg>
    <h3>LAUDRY ROOMS</h3>
    <p>Aliquam posuere pharetra elit eleifend faucibus. Suspendisse potenti. Proin ultrices placerat purus non accumsan. Duis at odio sit amet ex interdum dictum.</p>
  </div>

  <div class="service" style="left:94px;top:333px">
    <svg viewBox="0 0 28 28" width="28"><path d="M0 0h5v7h5v7h5v7h7v7H0z" fill="#0455a3"/></svg>
    <h3>STAIRS</h3>
    <p>Aliquam posuere pharetra elit eleifend faucibus. Suspendisse potenti. Proin ultrices placerat purus non accumsan. Duis at odio sit amet ex interdum dictum.</p>
  </div>
  <div class="service" style="left:317px;top:333px">
    <svg viewBox="0 0 24 28" width="24"><rect x="0" y="26" width="24" height="2" fill="#0455a3"/><rect x="2" y="0" width="20" height="27" fill="#0455a3"/><g fill="#fff"><rect x="5" y="3" width="4" height="4"/><rect x="11" y="3" width="4" height="4"/><rect x="5" y="9" width="4" height="4"/><rect x="11" y="9" width="4" height="4"/><rect x="5" y="15" width="4" height="4"/><rect x="11" y="15" width="4" height="4"/><rect x="8" y="21" width="6" height="6"/></g></svg>
    <h3>WINDOWS</h3>
    <p>Aliquam posuere pharetra elit eleifend faucibus. Suspendisse potenti. Proin ultrices placerat purus non accumsan. Duis at odio sit amet ex interdum dictum.</p>
  </div>
  <div class="service" style="left:540px;top:333px">
    <svg viewBox="0 0 30 30" width="30"><path d="M2 10h26v18M2 10v18" stroke="#0455a3" stroke-width="2" fill="none"/><rect x="16" y="14" width="10" height="6" fill="#0455a3"/><rect x="16" y="21" width="10" height="6" fill="#0455a3"/><path d="M14 8l6-6m0 0h-4m4 0v4" stroke="#0455a3" stroke-width="2" fill="none"/></svg>
    <h3>OFFICE ROOMS</h3>
    <p>Aliquam posuere pharetra elit eleifend faucibus. Suspendisse potenti. Proin ultrices placerat purus non accumsan. Duis at odio sit amet ex interdum dictum.</p>
  </div>
</section>

<section class="gallery">
  <div class="shot tower" role="img" aria-label="Dark glass office tower seen from below against a pale sky"></div>
  <div class="shot stone" role="img" aria-label="Pale stone office facade with tall windows"></div>
  <div class="shot office" role="img" aria-label="White office block with glass windows under a blue sky"></div>
  <div class="shot curve" role="img" aria-label="Curved white building with a green lawn in front"></div>
  <div class="shot lounge" role="img" aria-label="Bright living room with white sofa and wooden floor"></div>
  <div class="slide-arrow left"><svg width="7" height="12" viewBox="0 0 7 12"><path d="M6 1L1 6l5 5" stroke="#fff" fill="none"/></svg></div>
  <div class="slide-arrow right"><svg width="7" height="12" viewBox="0 0 7 12"><path d="M1 1l5 5-5 5" stroke="#fff" fill="none"/></svg></div>
</section>

<footer class="site-footer">
  <nav class="footer-nav"><span>Home</span><span>|</span><span>About Us</span><span>|</span><span>Services</span><span>|</span><span>Gallery</span><span>|</span><span>Contact Us</span></nav>
  <div class="copyright">Copyright © 2016 &nbsp;Bright Morrow Ltd. &nbsp;All rights reserved.</div>
  <div class="social"><span></span><span></span><span></span><span></span></div>
</footer>

</div>
</body>
</html>
```